Wesbite design for Investment Firm

We want a basic (clean) website that follows the form, fonts and colors of our attachments. This is for a financial investment management firm, but we have a boutique (anti-Wall Street) approach. Site should have an Home Page (Logo up top - room for basic copy on bottom, Philosophy Page (room for Quarterly Letter attachment and basic copy, Performance Page (room for Performance Overview and Performance Analysis and basic copy), Team Page, Commentary Page and Contact

Reason: Some designers have asked for an extension. Again, please only use image of Train Station or Train Station Logo in design.

Target Market(s)

Small and mid-size financial advisors from across the country

Industry/Entity Type

Financial

Number of Pages Required

5+ page

Font styles to use
Other font styles liked:
• Palotino Linotype

Colors
3176b5
cfdeed
ffffff

Requirements
Must have
• Please refer to existing site www.qlvor.example. Of note, this is too complex / cluttered. We simply want Blur, Grey and White consistent with attachments. The copy is pretty good, but will be simplified (and no quotes)
Should not have
• No images other than train station logo and / or train station image

```html
<!DOCTYPE html>
<html lang="en">
<head>
<meta charset="utf-8">
<title>Alder Crest Investment Company</title>
<link href="https://fonts.googleapis.com/css2?family=Crimson+Pro:ital,wght@0,400;0,600;1,400&family=Lato:wght@400;700&display=swap" rel="stylesheet">
<style>
:root{
  --blue:#3176b5;
  --blue-dark:#23578a;
  --blue-pale:#cfdeed;
  --card-pale:#eef3fa;
  --white:#ffffff;
  --grey-text:#555a60;
  --grey-head:#5d5f62;
  --line:#c9ccd0;
  --serif:"Crimson Pro", "Palatino Linotype", serif;
  --sans:"Lato", Arial, sans-serif;
}
*{box-sizing:border-box;margin:0;padding:0}
html,body{width:1200px;height:2375px;overflow:hidden}
body{position:relative;background:var(--white);font-family:var(--sans);color:var(--grey-text)}
.abs{position:absolute}
.center{text-align:center;left:0;width:1200px}

/* hero */
.hero{position:absolute;left:0;top:0;width:1200px;height:646px;
  background:linear-gradient(115deg,#6d9fcf 0%,#4b86c0 35%,#2f6aa6 65%,#3f78b4 100%)}
.hero-photo{position:absolute;inset:0;
  background:radial-gradient(ellipse at 72% 40%,rgba(20,50,90,.45),rgba(20,50,90,0) 55%),
             radial-gradient(ellipse at 15% 70%,rgba(255,255,255,.18),rgba(255,255,255,0) 50%)}
.brand{top:22px;font-family:var(--serif);font-size:38px;color:#1d4a78;font-variant:small-caps;letter-spacing:2px;font-weight:400}
.nav{position:absolute;left:76px;top:82px;width:1048px;height:41px;border-top:1px solid rgba(255,255,255,.8);border-bottom:1px solid rgba(255,255,255,.8);
  display:flex;justify-content:center;align-items:center;gap:0}
.nav a{font-family:var(--serif);font-size:19px;color:var(--white);text-decoration:none;padding:4px 19px;border-radius:6px}
.nav a.active{background:var(--white);color:var(--blue);padding:4px 24px}
.hero-title{top:298px;font-family:var(--serif);font-size:57px;color:var(--white);font-weight:400}
.hero-sub{top:377px;font-family:Arial,sans-serif;font-size:21px;color:var(--white)}
.cta{position:absolute;left:496px;top:430px;width:208px;height:46px;border-top:1px solid rgba(255,255,255,.8);border-bottom:1px solid rgba(255,255,255,.8);display:flex;align-items:center;justify-content:center}
.cta span{background:var(--white);color:var(--blue-dark);font-family:var(--serif);font-weight:600;font-size:19px;letter-spacing:.5px;padding:3px 12px;border-radius:5px}

/* headings */
.section-title{font-family:var(--serif);font-size:45px;color:var(--grey-head);font-weight:400}
.section-title em{font-style:normal;color:var(--blue)}

/* philosophy */
.cards{position:absolute;left:76px;top:765px;width:1048px;height:397px;display:flex;border:2px solid var(--line);box-shadow:0 10px 14px -8px rgba(0,0,0,.35)}
.card{flex:1;text-align:center;padding-top:30px;border-right:2px solid var(--line)}
.card:last-child{border-right:none}
.card.featured{background:var(--card-pale);border-top:4px solid var(--blue);margin-top:-2px}
.icon-circle{width:154px;height:154px;border-radius:50%;margin:0 auto;background:var(--white);border:1px solid #e3e6ea;
  box-shadow:0 8px 0 -1px var(--blue),0 10px 14px rgba(0,0,0,.15);display:flex;align-items:center;justify-content:center}
.card h3{font-family:var(--serif);font-weight:400;font-size:27px;color:var(--blue);margin-top:38px}
.card p{font-size:15.5px;line-height:25px;color:var(--grey-text);width:300px;margin:4px auto 0}
.more{display:inline-block;vertical-align:middle;margin-left:3px}

.quote{font-family:var(--serif);font-style:italic;font-size:20px;color:var(--blue);line-height:26px}
.quote-by{font-family:var(--serif);font-weight:600;font-size:18px;color:var(--blue-dark)}

/* welcome */
.welcome{position:absolute;left:0;top:1306px;width:1200px;height:396px;background:var(--blue-pale)}
.welcome p{font-size:15.5px;line-height:25px;color:var(--grey-text)}
.welcome .rule{position:absolute;left:410px;width:400px;top:274px;border-top:1px solid rgba(255,255,255,.9)}

/* team */
.team{position:absolute;left:76px;top:1818px;width:1048px;height:162px;border-bottom:1px solid var(--line);display:flex}
.member{width:270px;padding:18px 0 0 2px}
.member.featured{background:var(--white);box-shadow:0 4px 10px rgba(0,0,0,.25);padding-left:16px;width:270px}
.member + .member{border-left:1px solid var(--line)}
.member.next{padding-left:18px}
.member h4{font-family:var(--serif);font-weight:400;font-size:23px;color:var(--blue);margin-bottom:6px}
.member p{font-size:15px;line-height:25px;color:var(--grey-text);width:245px}
.arrow{position:absolute;top:1876px}

/* newsletter */
.newsletter{position:absolute;left:0;top:2123px;width:1200px;height:125px;background:var(--blue-pale)}
.nl-title{position:absolute;left:79px;top:40px;font-family:var(--serif);font-size:39px;color:var(--blue)}
.nl-form{position:absolute;left:299px;top:43px;width:823px;height:46px;border:1px solid var(--blue)}
.field{position:absolute;top:12px;height:22px;border-bottom:1px solid var(--blue);font-family:var(--serif);font-style:italic;font-size:16px;color:#6c7f94;padding-left:6px;line-height:22px}
.login{position:absolute;left:575px;top:6px;width:240px;height:30px;border:1px solid var(--blue);font-family:var(--serif);font-weight:600;font-size:19px;color:var(--blue-dark);text-align:center;line-height:28px;letter-spacing:1px}

/* footer */
.footer{position:absolute;left:0;top:2248px;width:1200px;height:127px;background:var(--blue);color:var(--white);font-size:15.5px}
.footer .rule{position:absolute;left:76px;width:1048px;border-top:1px solid rgba(255,255,255,.55)}
.footer .item{position:absolute;display:flex;align-items:center;gap:12px;line-height:25px}
.copy{position:absolute;left:0;width:1200px;top:88px;text-align:center;font-size:15px}
</style>
</head>
<body>

<header class="hero">
  <div class="hero-photo" role="img" aria-label="Blue-toned photo of a businessman touching a rising stock chart line"></div>
  <div class="abs center brand">Alder Crest Investment Company</div>
  <nav class="nav">
    <a class="active">Home</a><a>Philosophy</a><a>Performance</a><a>Team</a><a>Letters</a><a>Commentary</a><a>Contact Us</a>
  </nav>
  <h1 class="abs center hero-title">Your financial well-being matters.</h1>
  <p class="abs center hero-sub">Designing realistic Wealth Strategies that create future peace of mind.</p>
  <div class="cta"><span>CONTACT US NOW</span></div>
</header>

<h2 class="abs center section-title" style="top:692px">Our <em>Philosophy</em></h2>

<section class="cards">
  <div class="card">
    <div class="icon-circle">
      <svg width="76" height="60" viewBox="0 0 76 60" fill="none" stroke="#23578a" stroke-width="3">
        <circle cx="42" cy="10" r="5" fill="#23578a"/><circle cx="58" cy="26" r="5" fill="#23578a"/>
        <line x1="60" y1="6" x2="40" y2="30"/>
        <path d="M4 40 H18 L34 34 H48 C52 34 52 40 48 40 H34" fill="none"/>
        <path d="M4 40 V56 H20 L40 52 L68 38 C72 35 68 30 64 32 L50 40" fill="#23578a"/>
      </svg>
    </div>
    <h3>Buy at a Discount</h3>
    <p>Our proprietary investment research seeks to determine the appraised value of a company. Investments are then made at a significant discount...<svg class="more" width="14" height="12" viewBox="0 0 14 12" fill="none" stroke="#3176b5" stroke-width="2"><path d="M1 1l6 5 6-5M1 6l6 5 6-5"/></svg></p>
  </div>
  <div class="card featured">
    <div class="icon-circle">
      <svg width="76" height="66" viewBox="0 0 76 66" fill="none" stroke="#23578a" stroke-width="3.5" stroke-linejoin="round">
        <path d="M38 4 L72 62 H4 Z"/>
        <text x="38" y="52" text-anchor="middle" font-family="Lato, sans-serif" font-size="28" fill="#23578a" stroke="none">$</text>
      </svg>
    </div>
    <h3>Emphasis on Risk</h3>
    <p>Defining risk as the permanent loss of capital, we believe that the quality of investment decisions is far more important that the quantity...<svg class="more" width="14" height="12" viewBox="0 0 14 12" fill="none" stroke="#3176b5" stroke-width="2"><path d="M1 1l6 5 6-5M1 6l6 5 6-5"/></svg></p>
  </div>
  <div class="card">
    <div class="icon-circle">
      <svg width="76" height="66" viewBox="0 0 76 66" fill="none" stroke="#23578a" stroke-width="2.5">
        <circle cx="28" cy="12" r="7"/><circle cx="46" cy="8" r="6"/><circle cx="38" cy="28" r="9"/>
        <text x="38" y="33" text-anchor="middle" font-family="Lato, sans-serif" font-size="13" fill="#23578a" stroke="none">$</text>
        <path d="M6 28 V46 L22 62 H32 V50 L20 40"/>
        <path d="M70 28 V46 L54 62 H44 V50 L56 40"/>
      </svg>
    </div>
    <h3>Willingness to Hold Cash</h3>
    <p>Patience is necessary in the absence of obvious bargains, as entry price is a significant determinant of return...<svg class="more" width="14" height="12" viewBox="0 0 14 12" fill="none" stroke="#3176b5" stroke-width="2"><path d="M1 1l6 5 6-5M1 6l6 5 6-5"/></svg></p>
  </div>
</section>

<p class="abs center quote" style="top:1200px">"The stock market is filled with individuals who know the price of everything, but the value of nothing."</p>
<p class="abs center quote-by" style="top:1232px">– Walter Brandt</p>

<section class="welcome">
  <h2 class="abs center section-title" style="top:44px">Welcome <em>To Alder Crest Investment Company</em></h2>
  <p class="abs center" style="top:108px">We founded Alder Crest Investment Company in 1999, initially managing wealth from our family and friends in the town of Alder Crest. The high<br>expectations of our original investors is a key contributor to our value driven investment philosophy.</p>
  <p class="abs center" style="top:183px">Based in Fairhaven, TX, we manage assets for both individuals and institutions. Our investment methodology stresses absolute returns vs. relative<br>performance, blending a combination of fundamental analysis, discipline and patience with the goal of preserving and compounding capital.</p>
  <div class="rule"></div>
  <p class="abs center quote" style="top:288px">"An investment operation is one which, upon thorough analysis, promises safety of principal and an adequate return.<br>Operations not meeting these requirements are speculative."</p>
  <p class="abs center quote-by" style="top:348px">- Henry Caldwell, Patient Capital</p>
</section>

<h2 class="abs center section-title" style="top:1747px">Our <em>Team</em></h2>

<svg class="arrow" style="left:52px" width="14" height="30" viewBox="0 0 14 30" fill="none" stroke="#5d5f62" stroke-width="2.5"><path d="M12 2 L3 15 L12 28"/></svg>
<svg class="arrow" style="left:1134px" width="14" height="30" viewBox="0 0 14 30" fill="none" stroke="#3176b5" stroke-width="2.5"><path d="M2 2 L11 15 L2 28"/></svg>

<section class="team">
  <div class="member">
    <h4>Daniel P. Hale</h4>
    <p>Daniel is the cofounder and Managing Member of Alder Crest and serves as portfolio...<svg class="more" width="14" height="12" viewBox="0 0 14 12" fill="none" stroke="#3176b5" stroke-width="2"><path d="M1 1l6 5 6-5M1 6l6 5 6-5"/></svg></p>
  </div>
  <div class="member featured">
    <h4>Grant T. Olsen</h4>
    <p>Grant is a Member of Alder Crest, overseeing operations, marketing and client service...<svg class="more" width="14" height="12" viewBox="0 0 14 12" fill="none" stroke="#3176b5" stroke-width="2"><path d="M1 1l6 5 6-5M1 6l6 5 6-5"/></svg></p>
  </div>
  <div class="member next">
    <h4>Peter L. Avery</h4>
    <p>Peter has previously worked with Meridian Funds Group, Stonefield Asset Management...<svg class="more" width="14" height="12" viewBox="0 0 14 12" fill="none" stroke="#3176b5" stroke-width="2"><path d="M1 1l6 5 6-5M1 6l6 5 6-5"/></svg></p>
  </div>
  <div class="member next">
    <h4>Nora Whitfield</h4>
    <p>Nora serves as Chief Compliance Officer of Alder Crest. Previously, Nora worked at Meridian...<svg class="more" width="14" height="12" viewBox="0 0 14 12" fill="none" stroke="#3176b5" stroke-width="2"><path d="M1 1l6 5 6-5M1 6l6 5 6-5"/></svg></p>
  </div>
</section>

<p class="abs center quote" style="top:2009px">"Mimicking the herd invites regression to the mean."</p>
<p class="abs center quote-by" style="top:2040px">- Edwin Marsh</p>

<section class="newsletter">
  <h2 class="nl-title" style="font-weight:400">News Letter</h2>
  <div class="nl-form">
    <div class="field" style="left:18px;width:262px">Email</div>
    <div class="field" style="left:291px;width:263px">Password</div>
    <div class="login">LOGIN</div>
  </div>
</section>

<footer class="footer">
  <div class="rule" style="top:14px"></div>
  <div class="item" style="left:100px;top:20px">
    <svg width="14" height="20" viewBox="0 0 14 20" fill="#ffffff"><path d="M7 0C3 0 0 3 0 7c0 5 7 13 7 13s7-8 7-13c0-4-3-7-7-7zm0 10a3 3 0 110-6 3 3 0 010 6z"/></svg>
    <span>1250 Birch Hollow Avenue, Suite 610<br>Fairhaven, TX 75000</span>
  </div>
  <div class="item" style="left:536px;top:32px">
    <svg width="20" height="20" viewBox="0 0 20 20" fill="#ffffff"><path d="M4 1l4 4-2 3c1 2 3 4 6 6l3-2 4 4-3 3C8 19 1 12 1 4z"/></svg>
    <span>555.014.2290</span>
  </div>
  <div class="item" style="left:873px;top:32px">
    <svg width="20" height="15" viewBox="0 0 20 15" fill="none" stroke="#ffffff" stroke-width="1.8"><rect x="1" y="1" width="18" height="13" rx="1"/><path d="M1 2l9 7 9-7"/></svg>
    <span>info@aldercrest.example</span>
  </div>
  <div class="rule" style="top:76px"></div>
  <p class="copy">©Alder Crest Investment Company. 2017 - All Rights Reserved.</p>
</footer>

</body>
</html>
```